Start-up braucht modernes/hochwertiges Getränkeetikett
Zielgruppe
Wir sind ein modernes, nachhaltiges Start-up, welches eine neue Getränkekategorie auf den Markt bringt. Ein sogenanntes Elektrolyt-Getränk mit dem Namen FLUXO4. Es ist abgefüllt in eine 500 ml Flasche und enthält Magnesium, Kalzium, Kalium, und Natrium. Diese Stoffe (Elektrolyte) dienen der körperlichen Hydrierung. Zu Dehydrierung kann es durch Hitze, Alkohol, Sport oder Krankheit kommen. Krankheit liegt bei uns allerdings nicht im Fokus. In unserer Zielgruppe befinden sich hauptsächlich Personen im Alter von 18 - 29 Jahren.
Die Geschmacksrichtung ist Zitrone-Limette.
Aufgabenstellung
Das Etikett soll:
- MODERN, SCHLICHT und HOCHWERTIG sein, so dass es im Supermarkt hervorsticht
- erkenntlich machen, dass die Stoffe Magnesium, Natrium, Kalzium und Kalium enthalten sind
- sich farblich deutlich von der Farbe des Inhalts (weiß) abheben. (Vorzugsweise mit einem hellen Blau, türkis)
- für unsere junge Zielgruppe ansprechend sein
- ebenfalls auf die Geschmacksrichtung (Zitrone-Limette) hinweisen, und zwar so, dass wenn man eine weitere Geschmacksrichtung auf den Markt bringen möchte, diese leicht angepasst werden kann.
- nicht nach einem Energydrink oder einem typischen Sportgetränk aussehen
- unter dem Namen den Slogan 'Elektrolyt-Getränk' stehen haben
-Das Etikett ist nicht dursichtig sondern besteht aus Papier
Der Name sowie das Logo können selbstverständlich farblich verändert werden. Bei dem Logo können auch größere Änderungen vollzogen werden.
Bitte beachten Sie die unten zu stehenden Regler um sich einen guten Überblick über unsere Vorstellungen zu verschaffen. Die Platzierung des EAN-Code ist für ihr Design irrelevat .
Bei Unklarheiten gerne nachfragen!

```html
<!DOCTYPE html>
<html lang="de">
<head>
<meta charset="utf-8">
<title>FLUXO4 – Elektrolyt-Getränk Etikett</title>
<link rel="stylesheet" href="https://fonts.googleapis.com/css2?family=Roboto+Slab:wght@300;400;700;800&display=swap">
<style>
  :root {
    --bg-base: #c2e5ec;
    --bg-swirl: #b1dbe4;
    --ink: #1a1a1a;
    --panel: rgba(244, 250, 251, 0.88);
    --highlight: #ece35a;
  }
  * { margin: 0; padding: 0; box-sizing: border-box; }
  html, body {
    width: 1200px;
    height: 523px;
    overflow: hidden;
  }
  body {
    font-family: "Roboto Slab", Georgia, serif;
    color: var(--ink);
  }
  .label {
    position: relative;
    width: 1200px;
    height: 523px;
    overflow: hidden;
  }
  .label__backdrop {
    position: absolute;
    inset: 0;
    background:
      radial-gradient(ellipse 260px 120px at 180px 120px, var(--bg-swirl), transparent 70%),
      radial-gradient(ellipse 300px 140px at 1000px 400px, var(--bg-swirl), transparent 70%),
      radial-gradient(ellipse 220px 110px at 300px 420px, var(--bg-swirl), transparent 70%),
      radial-gradient(ellipse 240px 120px at 950px 110px, var(--bg-swirl), transparent 70%),
      var(--bg-base);
  }
  .brand {
    position: absolute;
    left: 0;
    width: 100%;
    top: 32px;
    text-align: center;
  }
  .brand__dot {
    display: block;
    margin: 0 auto;
    width: 78px;
    height: 78px;
  }
  .brand__name {
    display: block;
    margin-top: 14px;
    font-weight: 800;
    font-size: 46px;
    letter-spacing: 2px;
    line-height: 1;
  }
  .panel {
    position: absolute;
    left: 428px;
    width: 425px;
    background: var(--panel);
  }
  .panel--title {
    top: 227px;
    height: 55px;
    display: flex;
    align-items: center;
    justify-content: center;
    font-weight: 700;
    font-size: 30px;
  }
  .panel--flavour { top: 290px; height: 51px; }
  .panel--minerals { top: 349px; height: 124px; }
  .panel__key {
    position: absolute;
    left: 37px;
    font-weight: 700;
    font-size: 21px;
    line-height: 26px;
  }
  .panel--flavour .panel__key { top: 11px; }
  .panel--minerals .panel__key { top: 22px; }
  .flavour-tag {
    position: absolute;
    left: 228px;
    top: 11px;
    width: 180px;
    height: 28px;
  }
  .flavour-tag svg { position: absolute; inset: 0; }
  .flavour-tag__text {
    position: relative;
    display: block;
    padding-left: 17px;
    font-weight: 300;
    font-size: 21px;
    line-height: 28px;
  }
  .mineral-list {
    position: absolute;
    left: 244px;
    top: 9px;
    list-style: none;
    font-weight: 300;
    font-size: 22px;
    line-height: 25.6px;
  }
  .mineral-list li::before { content: "+ "; }
</style>
</head>
<body>
  <main class="label">
    <div class="label__backdrop" role="img" aria-label="Hellblauer marmorierter Hintergrund mit türkisen Schlieren"></div>

    <header class="brand">
      <svg class="brand__dot" viewBox="0 0 78 78" aria-hidden="true">
        <circle cx="39" cy="39" r="36" fill="none" stroke="#1a1a1a" stroke-width="2"/>
      </svg>
      <span class="brand__name">FLUXO4</span>
    </header>

    <section class="panel panel--title">Elektrolyt-Getränk</section>

    <section class="panel panel--flavour">
      <span class="panel__key">Geschmack:</span>
      <div class="flavour-tag">
        <svg viewBox="0 0 180 28" preserveAspectRatio="none" aria-hidden="true">
          <polygon points="5,1 180,0 173,28 0,28" fill="var(--highlight)"/>
        </svg>
        <span class="flavour-tag__text">Zitrone-Limette</span>
      </div>
    </section>

    <section class="panel panel--minerals">
      <span class="panel__key">Inhaltstoffe<br>die dich fit<br>halten:</span>
      <ul class="mineral-list">
        <li>Magnesium</li>
        <li>Natrium</li>
        <li>Kalzium</li>
        <li>Kalium</li>
      </ul>
    </section>
  </main>
</body>
</html>
```